Business Card Design Project - del varosi group

dear Sirs

we need business card design for our group ( DEL Varosi Group ) , i have got the Logo design of our group from pixel harbor in previous , so all need details relating to our group i think available with you, as well as the the chosen logo design

we hope to provide us with business card logo that to be appropaite and satisfactory to us .

thanks

note : logo design of our group is attached .
Updates

Reason: please extend the deadline of my project for additional 15 days because i didn't received appropriate design for our gruop yet . kindly beaware that i have received 77 design till now , supossed to send me 200-250 design at least . thanks

Target Market(s)

contents

name : Kerem EL Nadiri

position : Operation Manager

Industry/Entity Type

Business

Requirements
Must have

• person name

group logo
Nice to have
• logo color matching with back background

```html
<!DOCTYPE html>
<html lang="en">
<head>
<meta charset="utf-8">
<title>DEL Varosi Group – Business Card</title>
<link href="https://fonts.googleapis.com/css2?family=Yanone+Kaffeesatz:wght@300;400&family=Open+Sans:wght@400;600&display=swap" rel="stylesheet">
<style>
  :root {
    --page-bg: #e9eaec;
    --card-light: #f1f1f1;
    --card-mid: #dcdcdc;
    --brand-blue: #1e56a0;
    --ink-dark: #1f1f1f;
    --bar-text: #ffffff;
  }
  * { margin: 0; padding: 0; box-sizing: border-box; }
  html, body {
    width: 1067px;
    height: 1200px;
    overflow: hidden;
    background: var(--page-bg);
  }
  .sheet {
    position: relative;
    width: 1067px;
    height: 1200px;
  }
  .card {
    position: absolute;
    left: 83px;
    width: 900px;
    height: 514px;
    background: linear-gradient(135deg, var(--card-light) 0%, #e6e6e6 55%, var(--card-mid) 100%);
    box-shadow: 0 6px 22px rgba(0,0,0,0.18);
    overflow: hidden;
  }
  .card--front { top: 57px; }
  .card--back { top: 628px; }

  /* front: vertical group name */
  .front-brand {
    position: absolute;
    left: 178px;
    top: 49px;
    height: 432px;
    writing-mode: vertical-rl;
    transform: rotate(180deg);
    font-family: "Yanone Kaffeesatz", sans-serif;
    font-weight: 400;
    font-size: 66px;
    letter-spacing: 2px;
    color: var(--brand-blue);
    text-align: center;
    white-space: nowrap;
  }

  /* front: contact bars */
  .contact-bars {
    position: absolute;
    left: 442px;
    top: 39px;
    width: 446px;
    list-style: none;
  }
  .contact-bars li {
    height: 31px;
    margin-bottom: 5px;
    background: var(--brand-blue);
    color: var(--bar-text);
    font-family: "Open Sans", sans-serif;
    font-size: 15px;
    line-height: 31px;
    padding-left: 48px;
  }

  /* front: person block */
  .person {
    position: absolute;
    left: 452px;
    top: 328px;
    width: 400px;
    text-align: center;
  }
  .person__group {
    font-family: "Yanone Kaffeesatz", sans-serif;
    font-weight: 300;
    font-size: 36px;
    letter-spacing: 1px;
    color: var(--brand-blue);
    line-height: 42px;
  }
  .person__rule {
    height: 3px;
    background: var(--brand-blue);
  }
  .person__name {
    font-family: "Yanone Kaffeesatz", sans-serif;
    font-weight: 400;
    font-size: 38px;
    letter-spacing: 1px;
    color: var(--ink-dark);
    line-height: 44px;
  }
  .person__title {
    font-family: "Open Sans", sans-serif;
    font-weight: 600;
    font-size: 19px;
    color: var(--ink-dark);
    margin-top: 2px;
  }

  /* back: centred group name */
  .back-brand {
    position: absolute;
    left: 0;
    right: 0;
    top: 0;
    bottom: 0;
    display: flex;
    align-items: center;
    justify-content: center;
    gap: 22px;
  }
  .back-brand__mark {
    width: 34px;
    height: 34px;
    background: var(--brand-blue);
  }
  .back-brand__name {
    font-family: "Yanone Kaffeesatz", sans-serif;
    font-weight: 400;
    font-size: 80px;
    letter-spacing: 2px;
    color: var(--brand-blue);
  }
</style>
</head>
<body>
<main class="sheet">
  <section class="card card--front" aria-label="Business card front">
    <div class="front-brand">DEL VAROSI GROUP</div>

    <ul class="contact-bars">
      <li>Phone: 0123 456 789</li>
      <li>Fax: 0123 456 789</li>
      <li>info@yourdomain.com</li>
      <li>www.yourdomain.com</li>
      <li>P.O. Box: City name, etc.</li>
    </ul>

    <div class="person">
      <p class="person__group">DEL VAROSI GROUP</p>
      <div class="person__rule"></div>
      <p class="person__name">KEREM EL NADIRI</p>
      <div class="person__rule"></div>
      <p class="person__title">Operation Manager</p>
    </div>
  </section>

  <section class="card card--back" aria-label="Business card back">
    <div class="back-brand">
      <span class="back-brand__mark"></span>
      <span class="back-brand__name">DEL VAROSI GROUP</span>
    </div>
  </section>
</main>
</body>
</html>
```